TalkHarbor - Language Coaching Services

Sleek, innovative, trendy design for Language Coaching business.

TalkHarbor is a new UK based company that provides Language Coaching services. We offer highly personalized on-line and face to face language courses. We also impart learning techniques workshops based on the latest neuroscience research for second-language acquisition.

Target Market(s)

See attached info

Industry/Entity Type

Consulting

Contact Information for Business Card

TalkHarbor
DaniaKV@talkharbor.co.uk
TalkHarbor.co.uk
London, UK

Font styles to use
Sans Serif

```html
<!DOCTYPE html>
<html lang="en">
<head>
<meta charset="utf-8">
<title>TalkHarbor Business Card</title>
<link rel="stylesheet" href="https://fonts.googleapis.com/css2?family=Roboto:wght@400;500;700&display=swap">
<style>
  :root {
    --bg: #2b2e31;
    --card: #111214;
    --card-edge: #1c1e21;
    --blue: #1a9ad9;
    --blue-light: #2db4ef;
    --blue-dark: #0b6ea8;
    --ink: #f2f4f6;
    --ink-dark: #0d0e10;
  }
  * { margin: 0; padding: 0; box-sizing: border-box; }
  html, body {
    width: 1200px; height: 900px; overflow: hidden;
    background: var(--bg);
    font-family: "Roboto", Arial, sans-serif;
  }
  .canvas {
    position: relative; width: 1200px; height: 900px;
    display: flex; align-items: center; justify-content: center; gap: 50px;
  }
  .card {
    position: relative; width: 525px; height: 300px;
    border-radius: 22px; background: var(--card);
    overflow: hidden;
    box-shadow: 0 18px 40px rgba(0,0,0,.45);
  }

  /* Front */
  .front .speech-bubble { position: absolute; left: 34px; top: 22px; width: 170px; height: 150px; }
  .front .bubble-name {
    position: absolute; left: 58px; top: 22px; width: 146px; height: 122px;
    display: flex; align-items: center; justify-content: center;
    font-weight: 700; font-size: 21px; color: var(--ink-dark);
  }
  .front .base-band {
    position: absolute; left: 0; right: 0; bottom: 0; height: 24px;
    background: linear-gradient(90deg, var(--blue-dark), var(--blue-light));
  }
  .front .location {
    position: absolute; left: 22px; bottom: 44px;
    display: flex; align-items: center; gap: 6px;
    color: var(--ink); font-size: 15px; font-weight: 500;
  }
  .front .person { position: absolute; right: 34px; top: 96px; text-align: right; }
  .front .person-name { color: var(--blue); font-weight: 700; font-size: 24px; letter-spacing: .5px; }
  .front .person-role { color: var(--ink); font-weight: 500; font-size: 15px; margin-top: 4px; }
  .front .accent-dash {
    position: absolute; right: 40px; top: 178px; width: 16px; height: 3px; background: var(--blue);
  }
  .front .contacts {
    position: absolute; right: 26px; top: 198px; list-style: none;
    display: flex; flex-direction: column; gap: 8px; align-items: flex-end;
  }
  .front .contacts li {
    display: flex; align-items: center; gap: 10px;
    color: var(--ink); font-size: 15px; font-weight: 500;
  }
  .front .contacts svg { width: 18px; height: 18px; }

  /* Back */
  .back { display: flex; align-items: center; justify-content: center; gap: 16px; }
  .back .brand-dot {
    width: 62px; height: 62px; border-radius: 50%;
    border: 5px solid var(--blue);
  }
  .back .brand-name {
    color: var(--blue); font-weight: 700; font-size: 46px; letter-spacing: 1px;
  }
</style>
</head>
<body>
<main class="canvas">
  <section class="card front" aria-label="Business card front">
    <svg class="speech-bubble" viewBox="0 0 170 150" aria-hidden="true">
      <defs>
        <linearGradient id="bubbleFill" x1="0" y1="0" x2="1" y2="1">
          <stop offset="0" stop-color="#2db4ef"/>
          <stop offset="1" stop-color="#0b72b0"/>
        </linearGradient>
      </defs>
      <path d="M36 0 H154 Q170 0 170 16 V106 Q170 122 154 122 H52 Q36 122 36 106 V120 L0 122 L36 98 V16 Q36 0 52 0 Z" fill="url(#bubbleFill)"/>
    </svg>
    <div class="bubble-name">TalkHarbor</div>

    <div class="location">
      <svg width="12" height="16" viewBox="0 0 12 16" aria-hidden="true">
        <path d="M6 0a6 6 0 0 0-6 6c0 4.5 6 10 6 10s6-5.5 6-10a6 6 0 0 0-6-6zm0 8.5A2.5 2.5 0 1 1 6 3.5a2.5 2.5 0 0 1 0 5z" fill="#1a9ad9"/>
      </svg>
      London, UK
    </div>

    <div class="person">
      <p class="person-name">MARCUS ELLERY</p>
      <p class="person-role">Manager</p>
    </div>
    <span class="accent-dash"></span>

    <ul class="contacts">
      <li>020 555 0148
        <svg viewBox="0 0 18 18" aria-hidden="true"><path d="M4 1.5l3 3-1.6 2.2a10 10 0 0 0 5.9 5.9L13.5 11l3 3-2 2.4C8.5 16 2 9.5 1.6 3.5Z" fill="#1a9ad9"/></svg>
      </li>
      <li>DaniaKV@talkharbor.co.uk
        <svg viewBox="0 0 18 18" aria-hidden="true"><rect x="1" y="3.5" width="16" height="11" rx="1" fill="#1a9ad9"/><path d="M1.5 4.5 9 10l7.5-5.5" fill="none" stroke="#111214" stroke-width="1.4"/></svg>
      </li>
      <li>TalkHarbor.co.uk
        <svg viewBox="0 0 18 18" aria-hidden="true"><circle cx="9" cy="9" r="8" fill="#1a9ad9"/><g fill="none" stroke="#111214" stroke-width="1.1"><ellipse cx="9" cy="9" rx="3.5" ry="8"/><path d="M1 9h16M2.5 5h13M2.5 13h13"/></g></svg>
      </li>
    </ul>
    <div class="base-band"></div>
  </section>

  <section class="card back" aria-label="Business card back">
    <span class="brand-dot"></span>
    <p class="brand-name">TALKHARBOR</p>
  </section>
</main>
</body>
</html>
```